Mobile Fitness snd Therapy Business Card Design

I need a business card designed for my mobile fitness and therapy business.

Please view the images that I have uploaded. I like the simplicity of the design that I have attached. I adapted it with my information

Target Market(s)

Those seeking personal training, injury rehabilitation or massage therapy.

Industry/Entity Type

Business

Contact Information for Business Card

Derek Fulham - MSc, CAT(C), RMT, CSCS, Pn2
e-mail: derek@vantrelo.com
website: www.vantrelo.com
instagram: @derek_fulham

Font styles to use
Sans Serif

Colors
3176b5
0355a3

Requirements
Must have
• "Contact us to receive a FREE assessment"
• Services offered:
• Personal Training
• Golf Fitness
• Injury Rehab
• Massage Therapy
• Yoga
Nice to have
• Consistent colours with brand
• - Dark Blue: #232837
• - Blue: #5096f0
• Consistent look/feel with the website: www.vantrelo.com

```html
<!DOCTYPE html>
<html lang="en">
<head>
<meta charset="utf-8">
<title>Vantrelo Business Card</title>
<link rel="stylesheet" href="https://fonts.googleapis.com/css2?family=Source+Sans+3:wght@400;600;700&display=swap">
<style>
  :root {
    --backdrop: #a6a6a6;
    --card-white: #ffffff;
    --brand-blue: #2a5bd7;
    --ink-dark: #232837;
    --rule-grey: #cfcfcf;
    --text-white: #ffffff;
  }
  * { margin: 0; padding: 0; box-sizing: border-box; }
  html, body { width: 1200px; height: 900px; overflow: hidden; }
  body {
    background: var(--backdrop);
    font-family: "Source Sans 3", "Myriad Pro", Arial, sans-serif;
    position: relative;
  }
  .card {
    position: absolute;
    top: 306px;
    width: 440px;
    height: 271px;
    box-shadow: 3px 4px 6px rgba(0,0,0,0.45);
    overflow: hidden;
  }
  .card-front { left: 149px; background: var(--card-white); }
  .card-back { left: 608px; background: var(--brand-blue); }

  .brand { position: absolute; line-height: 1; }
  .brand-name {
    font-weight: 700;
    font-size: 27px;
    letter-spacing: 2.5px;
  }
  .brand-tagline {
    font-weight: 700;
    font-size: 8.5px;
    letter-spacing: 1.6px;
    margin-top: 4px;
  }
  .card-front .brand { left: 31px; top: 25px; color: var(--ink-dark); }
  .card-back .brand { left: 0; right: 0; top: 20px; text-align: center; color: var(--text-white); }

  .holder { position: absolute; right: 29px; top: 25px; text-align: right; }
  .holder-name {
    font-weight: 600; font-size: 17px; color: var(--ink-dark);
    text-transform: uppercase; line-height: 1.1;
  }
  .holder-credentials { font-size: 12.5px; color: var(--brand-blue); margin-top: 1px; }

  .divider {
    position: absolute; left: 29px; right: 29px; top: 184px;
    height: 1px; background: var(--rule-grey);
  }
  .contact-list { position: absolute; left: 29px; top: 193px; list-style: none; }
  .contact-list li {
    display: flex; align-items: center; gap: 5px;
    font-size: 13.5px; color: var(--ink-dark); line-height: 16.5px;
  }
  .contact-icon { width: 11px; height: 11px; flex: none; }

  .services {
    position: absolute; left: 148px; top: 98px;
    color: var(--text-white); font-weight: 600; font-size: 17.5px; line-height: 20px;
    list-style: none;
  }
  .services-title { font-size: 19px; text-decoration: underline; text-underline-offset: 2px; margin-bottom: 1px; }

  .offer-band {
    position: absolute; left: 0; right: 0; bottom: 0; height: 40px;
    background: var(--card-white);
    display: flex; align-items: center; justify-content: center;
    color: var(--brand-blue); font-weight: 600; font-size: 17px;
  }
</style>
</head>
<body>
  <section class="card card-front">
    <div class="brand">
      <div class="brand-name">VANTRELO</div>
      <div class="brand-tagline">NUTRITION - FITNESS - HEALTH</div>
    </div>
    <div class="holder">
      <div class="holder-name">Derek Fulham</div>
      <div class="holder-credentials">MSc, CAT(C), RMT, CSCS, Pn2</div>
    </div>
    <div class="divider"></div>
    <ul class="contact-list">
      <li>
        <svg class="contact-icon" viewBox="0 0 11 11" aria-hidden="true">
          <rect width="11" height="11" rx="2" fill="#232837"/>
          <rect x="2" y="3" width="7" height="5" fill="none" stroke="#fff" stroke-width="1"/>
          <path d="M2 3 L5.5 6 L9 3" fill="none" stroke="#fff" stroke-width="1"/>
        </svg>
        derek@vantrelo.com
      </li>
      <li>
        <svg class="contact-icon" viewBox="0 0 11 11" aria-hidden="true">
          <rect width="11" height="11" rx="2" fill="#232837"/>
          <circle cx="5.5" cy="5.5" r="3.2" fill="none" stroke="#fff" stroke-width="1"/>
          <path d="M2.3 5.5 H8.7 M5.5 2.3 V8.7" stroke="#fff" stroke-width="0.8"/>
        </svg>
        www.vantrelo.com
      </li>
      <li>
        <svg class="contact-icon" viewBox="0 0 11 11" aria-hidden="true">
          <rect width="11" height="11" rx="2" fill="#232837"/>
        </svg>
        @derek_fulham
      </li>
    </ul>
  </section>

  <section class="card card-back">
    <div class="brand">
      <div class="brand-name">VANTRELO</div>
      <div class="brand-tagline">NUTRITION - FITNESS - HEALTH</div>
    </div>
    <ul class="services">
      <li class="services-title">Services offered</li>
      <li>- Personal Training</li>
      <li>- Golf Fitness</li>
      <li>- Injury Rehab</li>
      <li>- Massage Therapy</li>
      <li>- Yoga</li>
    </ul>
    <div class="offer-band">Contact us to receive a FREE assessment</div>
  </section>
</body>
</html>
```